Business Card Design

We need a design for business cards for our company. We have a logo. We teach EMT's and we are based out of Virginia. The information that will need to add would be, name, title, phone number, email, address. On the back of the business card would be "Trained to care, ready to respond"

Target Market(s)

People that want to become EMT's

Colors

Designer to choose colors to be used in the design.

Requirements
Must have
• company logo

```html
<!DOCTYPE html>
<html lang="en">
<head>
<meta charset="utf-8">
<title>Rescue Ready Academy – Business Card</title>
<link rel="stylesheet" href="https://fonts.googleapis.com/css2?family=Montserrat:wght@500;600;700&family=Open+Sans:wght@400;600&display=swap">
<style>
  :root {
    --brand-red: #c21f30;
    --brand-red-dark: #a91a29;
    --ink: #4a4a4a;
    --muted: #7a7a7a;
    --band-grey: #a5a5a8;
    --paper: #fcf8f8;
    --backdrop: #e9e9ea;
  }
  * { box-sizing: border-box; margin: 0; padding: 0; }
  html, body { width: 1200px; height: 782px; overflow: hidden; }
  body {
    background: var(--backdrop);
    font-family: "Open Sans", Arial, sans-serif;
    position: relative;
  }
  .card {
    position: absolute;
    width: 525px;
    height: 300px;
    top: 241px;
    box-shadow: 0 6px 18px rgba(0,0,0,.18);
    overflow: hidden;
  }
  .card--front { left: 50px; background: var(--paper); }
  .card--back { left: 625px; background: var(--brand-red); }

  /* Front */
  .brand {
    position: absolute;
    left: 30px; top: 92px;
    display: flex; align-items: center; gap: 10px;
  }
  .brand__mark {
    width: 14px; height: 14px;
    background: var(--brand-red);
    border-radius: 50%;
    flex: none;
  }
  .brand__name {
    font-family: "Montserrat", Arial, sans-serif;
    font-weight: 700;
    font-size: 20px;
    color: var(--brand-red);
    letter-spacing: .3px;
    line-height: 1.1;
  }
  .divider {
    position: absolute;
    left: 262px; top: 50px;
    width: 1px; height: 160px;
    background: #d9d4d4;
  }
  .contact {
    position: absolute;
    left: 286px; top: 66px;
    width: 225px;
    color: var(--ink);
  }
  .contact__name {
    font-family: "Montserrat", Arial, sans-serif;
    font-weight: 700;
    font-size: 19px;
    color: var(--brand-red);
    letter-spacing: .4px;
    line-height: 1;
  }
  .contact__title {
    font-size: 14px;
    color: var(--muted);
    margin-top: 3px;
    margin-bottom: 10px;
  }
  .contact__line {
    display: flex; align-items: center; gap: 7px;
    font-size: 14.5px;
    line-height: 1.35;
    white-space: nowrap;
  }
  .contact__line svg { width: 14px; height: 14px; flex: none; }
  .contact__address {
    font-size: 14.5px;
    line-height: 1.3;
    margin-top: 8px;
    white-space: nowrap;
  }
  .bands { position: absolute; left: 0; bottom: 0; width: 100%; height: 40px; }

  /* Back */
  .back__pattern {
    position: absolute; inset: 0;
    background: linear-gradient(135deg, var(--brand-red) 0%, var(--brand-red-dark) 100%);
  }
  .back__tagline {
    position: absolute;
    left: 0; right: 0; bottom: 78px;
    text-align: center;
    font-family: "Montserrat", Arial, sans-serif;
    font-weight: 600;
    font-size: 15px;
    color: #fff;
    letter-spacing: .4px;
  }
</style>
</head>
<body>

<section class="card card--front" aria-label="Business card front">
  <div class="brand">
    <span class="brand__mark"></span>
    <span class="brand__name">RESCUE READY<br>ACADEMY</span>
  </div>

  <div class="divider"></div>

  <div class="contact">
    <p class="contact__name">DANIEL HART</p>
    <p class="contact__title">Managing Director</p>
    <p class="contact__line">
      <svg viewBox="0 0 16 16" aria-hidden="true"><path fill="#c21f30" d="M3.2 1.5l2.4-.4 1.3 3.3-1.6 1.2c.8 1.7 2.1 3 3.8 3.8l1.2-1.6 3.3 1.3-.4 2.4c-.1.6-.7 1-1.3 1C6.4 12.3 3.7 9.6 2.2 2.8c0-.6.4-1.2 1-1.3z"/></svg>
      044-555 010 222
    </p>
    <p class="contact__line">
      <svg viewBox="0 0 16 16" aria-hidden="true"><rect x="1" y="3" width="14" height="10" rx="1" fill="#c21f30"/><path d="M1.5 3.8L8 8.6l6.5-4.8" fill="none" stroke="#fff" stroke-width="1.3"/></svg>
      hello@rescueready.com
    </p>
    <p class="contact__address">18 Harbor Lane, Suite 4<br>23456, Riverton</p>
  </div>

  <svg class="bands" viewBox="0 0 525 40" preserveAspectRatio="none" aria-hidden="true">
    <polygon points="0,18 300,18 292,34 0,34" fill="var(--band-grey)"/>
    <polygon points="304,14 525,14 525,40 290,40" fill="var(--brand-red)"/>
  </svg>
</section>

<section class="card card--back" aria-label="Business card back">
  <div class="back__pattern" role="img" aria-label="Repeating pattern of the company symbol in a lighter red"></div>
  <p class="back__tagline">TRAINED TO CARE, READY TO RESPOND</p>
</section>

</body>
</html>
```